Corinnehabbard.com

1. Conceptualization and designing of the site Homepage. The Homepage design will be completely customized and based on your design instructions (i.e. preferred colors, links to reference sites that you want us to take reference from if any etc) and the recently completed logo design.
2. Upon homepage design approval, based on it we will be creating the layout for the other 4 site inner pages (i.e. About page, Contact page, Services page, and Insights (publications, media).
3. Once all the inner page designs are approved, we will get the designs built (will make sure that the site is completely Responsive - works on all devices) within your provided WIX account.
4. We will add the static text and images provided by you to the Home page, About page, Contact page, and the Services page. For the 2 Insights sub-pages, we will add 1-2 sample Publications and Media entries.
once you confirm the total number of required entries for the 2 sub-pages, I will accordingly quote you on the same
5. Integration of a Contact form on the Contact page that will email the filled in details to your mail id.

```html
<!DOCTYPE html>
<html lang="en">
<head>
<meta charset="utf-8">
<title>Corinne Habbard Consulting</title>
<link href="https://fonts.googleapis.com/css2?family=Montserrat:wght@300;400;600;700&family=Arimo:wght@400;700&display=swap" rel="stylesheet">
<style>
:root{
  --green:#0f9140;
  --green-light:#33a852;
  --orange:#f29100;
  --blue:#0a96dc;
  --ink:#1b1b1b;
  --text:#333;
  --grey-bg:#f2f2f2;
  --footer:#060b1a;
  --white:#fff;
}
*{margin:0;padding:0;box-sizing:border-box}
html,body{width:1200px;height:3603px;overflow:hidden}
body{position:relative;background:var(--white);font-family:Arimo,Arial,sans-serif;color:var(--text)}
.abs{position:absolute}
.heading{font-family:Montserrat,sans-serif;font-weight:600;color:var(--ink)}
.btn{position:absolute;background:var(--orange);color:#fff;font-family:Montserrat,sans-serif;font-weight:600;font-size:16px;display:flex;align-items:center;justify-content:center}
.brand{position:absolute;display:flex;align-items:center;gap:10px;font-family:Montserrat,sans-serif;font-weight:600;font-size:15px;color:var(--blue);line-height:1.15}
.brand .dot{width:34px;height:34px;border-radius:50%;background:var(--blue);flex:none}
/* header */
.site-header{position:absolute;left:0;top:0;width:1200px;height:115px;background:#fff}
.nav{position:absolute;top:45px;display:flex;font-size:15px;color:#222}
.nav a{color:inherit;text-decoration:none;margin-right:38px}
/* hero */
.hero{position:absolute;left:0;top:115px;width:1200px;height:690px;overflow:hidden}
.hero-photo{position:absolute;inset:0;background:linear-gradient(90deg,#169a45 0%,#2fa452 45%,#8d8f8c 60%,#b6b0a6 80%,#d8d4cc 100%)}
.hero-title{position:absolute;left:113px;top:205px;color:#fff;font-family:Montserrat,sans-serif;font-size:54px;line-height:58px}
.hero-title b{font-weight:700;display:block}
.hero-title span{font-weight:300}
.hero-text{position:absolute;left:114px;top:345px;width:450px;color:#fff;font-size:15px;line-height:26px}
.dots{position:absolute;left:565px;top:622px;display:flex;gap:8px}
.dots i{width:14px;height:14px;border-radius:50%;background:#fff;display:block}
.dots i.on{background:var(--orange)}
/* about */
.underline{position:absolute;height:4px;background:var(--blue);border-radius:2px}
.about-text{position:absolute;left:117px;top:968px;width:425px;font-size:15px;line-height:26.6px}
/* services */
.services{position:absolute;left:0;top:1449px;width:1200px;height:626px;background:linear-gradient(180deg,#e9e9e9,#dcdedd 60%,#e6e6e6)}
.card{position:absolute;width:227px;height:316px;background:#fff;padding:26px 20px 0 28px;overflow:hidden}
.card h3{font-family:Montserrat,sans-serif;font-weight:600;font-size:17px;line-height:23px;color:#222;margin:12px 0 12px}
.card p{font-size:13px;line-height:19px;color:#333}
.card .corner{position:absolute;right:0;bottom:0;width:58px;height:72px}
.card.active{background:var(--green)}
.card.active h3,.card.active p{color:#fff}
.icon{width:48px;height:48px}
/* insights */
.post{position:absolute;top:2231px;width:305px}
.post .img{width:298px;height:215px;position:relative}
.post .frame{position:absolute;left:8px;top:6px;width:298px;height:215px;border-right:6px solid var(--blue);border-bottom:6px solid var(--blue)}
.post .date{margin-top:32px;font-size:13px;color:#333}
.post h4{font-family:Montserrat,sans-serif;font-weight:600;font-size:19px;line-height:29px;color:#111;margin-top:12px}
.post .more{display:inline-block;margin-top:14px;font-family:Montserrat,sans-serif;font-weight:600;font-size:14px;color:var(--orange);text-decoration:underline}
/* contact */
.contact{position:absolute;left:0;top:2660px;width:1200px;height:568px;background:var(--grey-bg)}
.field{position:absolute;background:#fff;font-size:13px;color:#555;padding:22px 19px;box-shadow:0 1px 3px rgba(0,0,0,.06)}
/* footer */
.footer{position:absolute;left:0;top:3228px;width:1200px;height:375px;background:var(--footer);color:#fff}
.info{position:absolute;top:100px;display:flex;align-items:center;gap:24px;font-size:15px;line-height:22px}
.info .ring{width:46px;height:46px;border:1px solid #1d63b0;border-radius:50%;display:flex;align-items:center;justify-content:center;flex:none}
.rule{position:absolute;left:112px;width:977px;height:1px;background:#2a3045}
.fnav{position:absolute;top:230px;right:111px;display:flex;gap:50px;font-size:17px}
.legal{position:absolute;top:318px;font-size:13px}
</style>
</head>
<body>

<header class="site-header">
  <div class="brand" style="left:113px;top:38px"><i class="dot"></i><span>CORINNE HABBARD<br>CONSULTING</span></div>
  <nav class="nav" style="left:460px"><a>Home</a><a>About us</a><a>Insights</a><a>Services</a><a>Contact us</a></nav>
  <div class="btn" style="left:986px;top:34px;width:103px;height:46px">Log in</div>
</header>

<section class="hero">
  <div class="hero-photo" role="img" aria-label="Business team meeting around a table with documents"></div>
  <svg class="abs" style="left:0;top:560px" width="1200" height="130" viewBox="0 0 1200 130">
    <path d="M0 140 L0 95 C300 170 800 150 1200 0 L1200 140 Z" fill="#fff"/>
    <path d="M0 95 C300 170 800 150 1200 0 L1200 12 C800 165 300 185 0 110 Z" fill="var(--blue)"/>
  </svg>
  <h1 class="hero-title"><b>Corinne Habbard</b><span>Consulting</span></h1>
  <p class="hero-text">Lorem ipsum dolor sit amet, consectetur adipiscing elit, sed do eiusmod tempor incididunt ut labore et dolore magna aliqua.</p>
  <div class="btn" style="left:112px;top:425px;width:126px;height:46px">Get started</div>
  <div class="dots"><i></i><i class="on"></i><i></i></div>
</section>

<section>
  <h2 class="heading abs" style="left:116px;top:880px;font-size:34px">About Us</h2>
  <div class="underline" style="left:117px;top:926px;width:60px"></div>
  <p class="about-text">Lorem ipsum dolor sit amet, consectetur adipiscing elit, sed do eiusmod tempor incididunt ut labore et dolore magna aliqua. Ut enim ad minim veniam, quis nostrud exercitation ullamco laboris nisi ut aliquip ex ea commodo consequat. Duis aute irure dolor in reprehenderit in voluptate velit esse cillum dolore eu fugiat nulla pariatur. Excepteur sint occaecat cupidatat non proident, sunt in culpa qui officia deserunt mollit anim id est laborum."</p>
  <div class="btn" style="left:113px;top:1214px;width:129px;height:46px">Learn More</div>
  <svg class="abs" style="left:588px;top:874px" width="510" height="472" viewBox="0 0 510 472">
    <polygon points="60,0 510,0 460,472 0,472" fill="var(--orange)"/>
  </svg>
  <div class="abs" role="img" aria-label="Colleagues talking around a meeting table in an office" style="left:590px;top:874px;width:492px;height:472px;background:linear-gradient(135deg,#9a8f80,#c8c3bb 50%,#e4e2de);clip-path:polygon(64px 0,492px 0,444px 472px,0 472px)"></div>
</section>

<section class="services">
  <h2 class="heading abs" style="left:0;width:1200px;text-align:center;top:68px;font-size:34px">Our Services</h2>
  <div class="underline" style="left:571px;top:114px;width:60px"></div>

  <div class="card" style="left:113px;top:171px">
    <svg class="icon" viewBox="0 0 48 48" fill="none" stroke="#222" stroke-width="2"><circle cx="14" cy="14" r="7"/><circle cx="30" cy="12" r="5"/><rect x="24" y="26" width="18" height="18"/><path d="M28 32h10M28 37h10"/></svg>
    <h3>Sed ut perspiciatis</h3>
    <p>Lorem ipsum dolor sit amet, consectetur adipiscing elit, sed do eiusmod tempor incididunt ut labore et dolore magna aliqua. Ut enim ad minim veniam, quis nostrud exercitation ullamco laboris</p>
    <svg class="corner" viewBox="0 0 58 72"><polygon points="58,0 58,72 0,72" fill="var(--orange)"/><path d="M39 50l5 5-5 5" stroke="#fff" stroke-width="2" fill="none"/></svg>
  </div>

  <div class="card" style="left:362px;top:224px">
    <svg class="icon" viewBox="0 0 48 48" fill="none" stroke="#222" stroke-width="2"><circle cx="24" cy="20" r="12"/><circle cx="24" cy="20" r="5"/><path d="M18 32v8h12v-8"/></svg>
    <h3>Sed ut perspiciatis</h3>
    <p>Lorem ipsum dolor sit amet, consectetur adipiscing elit, sed do eiusmod tempor incididunt ut labore et dolore magna aliqua. Ut enim ad minim veniam, quis nostrud exercitation ullamco laboris</p>
    <svg class="corner" viewBox="0 0 58 72"><polygon points="58,0 58,72 0,72" fill="var(--orange)"/><path d="M39 50l5 5-5 5" stroke="#fff" stroke-width="2" fill="none"/></svg>
  </div>

  <div class="card active" style="left:612px;top:171px">
    <svg class="icon" viewBox="0 0 48 48" fill="none" stroke="#fff" stroke-width="2"><path d="M4 44h40M10 44V28h8v16M22 44V20h8v24M34 44V12h8v32"/><circle cx="12" cy="14" r="5"/></svg>
    <h3>Sed ut perspiciatis unde omnis</h3>
    <p>Lorem ipsum dolor sit amet, consectetur adipiscing elit, sed do eiusmod tempor incididunt ut labore et dolore magna aliqua. Ut enim ad minim veniam, quis nostrud exercitation ullamco laboris</p>
    <svg class="corner" viewBox="0 0 58 72"><polygon points="58,0 58,72 0,72" fill="#fff"/><path d="M39 50l5 5-5 5" stroke="var(--blue)" stroke-width="2" fill="none"/></svg>
  </div>

  <div class="card" style="left:862px;top:224px">
    <svg class="icon" viewBox="0 0 48 48" fill="none" stroke="#222" stroke-width="2"><circle cx="12" cy="12" r="6"/><circle cx="36" cy="12" r="6"/><circle cx="36" cy="36" r="6"/><rect x="4" y="28" width="16" height="16"/><path d="M18 12h12M36 18v12"/></svg>
    <h3>lorem ipsum dolor sit amet</h3>
    <p>Lorem ipsum dolor sit amet, consectetur adipiscing elit, sed do eiusmod tempor incididunt ut labore et dolore magna aliqua. Ut enim ad minim veniam, quis nostrud exercitation ullamco laboris</p>
    <svg class="corner" viewBox="0 0 58 72"><polygon points="58,0 58,72 0,72" fill="var(--orange)"/><path d="M39 50l5 5-5 5" stroke="#fff" stroke-width="2" fill="none"/></svg>
  </div>
</section>

<section>
  <h2 class="heading abs" style="left:0;width:1200px;text-align:center;top:2146px;font-size:34px">Our Insights</h2>
  <div class="underline" style="left:571px;top:2192px;width:60px"></div>

  <article class="post" style="left:113px">
    <div class="img"><div class="frame"></div><div class="abs" role="img" aria-label="Team discussing at a conference table" style="inset:0;background:linear-gradient(135deg,#d9d6cf,#9d8f7f 60%,#c9c4bb)"></div></div>
    <p class="date">APR 22, 2024</p>
    <h4>Lorem ipsum dolor sit amet consectetur</h4>
    <a class="more">LEARN MORE</a>
  </article>
  <article class="post" style="left:452px">
    <div class="img"><div class="frame"></div><div class="abs" role="img" aria-label="Two colleagues reviewing a tablet together" style="inset:0;background:linear-gradient(135deg,#c9c3b9,#a7794a 55%,#d6d2cb)"></div></div>
    <p class="date">APR 22, 2024</p>
    <h4>Lorem ipsum dolor sit amet consectetur</h4>
    <a class="more">LEARN MORE</a>
  </article>
  <article class="post" style="left:792px">
    <div class="img"><div class="frame"></div><div class="abs" role="img" aria-label="Business people meeting in a glass office" style="inset:0;background:linear-gradient(135deg,#5c6670,#8d969c 50%,#4a4f58)"></div></div>
    <p class="date">APR 22, 2024</p>
    <h4>Lorem ipsum dolor sit amet consectetur</h4>
    <a class="more">LEARN MORE</a>
  </article>
</section>

<section class="contact">
  <h2 class="heading abs" style="left:0;width:1200px;text-align:center;top:52px;font-size:34px">Contact us</h2>
  <div class="field" style="left:179px;top:153px;width:408px;height:62px">First Name</div>
  <div class="field" style="left:613px;top:153px;width:409px;height:62px">Last Name</div>
  <div class="field" style="left:179px;top:239px;width:408px;height:62px">Phone</div>
  <div class="field" style="left:613px;top:239px;width:409px;height:62px">Email</div>
  <div class="field" style="left:179px;top:325px;width:843px;height:113px">Message</div>
  <div class="btn" style="left:536px;top:463px;width:128px;height:46px">Submit</div>
</section>

<footer class="footer">
  <div class="info" style="left:155px">
    <span class="ring"><svg width="14" height="12" viewBox="0 0 14 12"><rect x="0" y="0" width="14" height="12" rx="1" fill="#1d63b0"/><path d="M0 1l7 6 7-6" stroke="#fff" fill="none"/></svg></span>
    <span>info@Corinnehabbard.com</span>
  </div>
  <div class="info" style="left:481px">
    <span class="ring"><svg width="14" height="14" viewBox="0 0 24 24"><path d="M6 2l4 4-2 3c1 3 4 6 7 7l3-2 4 4-3 4C10 22 2 14 2 5z" fill="#1d63b0"/></svg></span>
    <span>+1 888 888 8888</span>
  </div>
  <div class="info" style="left:807px">
    <span class="ring"><svg width="12" height="16" viewBox="0 0 12 16"><path d="M6 0a6 6 0 0 1 6 6c0 4-6 10-6 10S0 10 0 6a6 6 0 0 1 6-6z" fill="#1d63b0"/><circle cx="6" cy="6" r="2" fill="#060b1a"/></svg></span>
    <span>22Y,&nbsp; Loremlipsum is dum<br>54646</span>
  </div>
  <div class="rule" style="top:183px"></div>
  <div class="brand" style="left:122px;top:222px"><i class="dot"></i><span>CORINNE HABBARD<br>CONSULTING</span></div>
  <nav class="fnav"><span>Home</span><span>About us</span><span>Insights</span><span>Services</span><span>Contact Us</span></nav>
  <div class="rule" style="top:295px"></div>
  <p class="legal" style="left:112px">© 2024 Copyright | All Rights Reserved.</p>
  <p class="legal" style="left:851px">Privacy Policy&nbsp;&nbsp;&nbsp;&nbsp;&nbsp;&nbsp;&nbsp;&nbsp;&nbsp;&nbsp;|&nbsp;&nbsp;&nbsp;&nbsp;&nbsp;&nbsp;&nbsp;&nbsp;&nbsp;&nbsp;Terms Of Use</p>
</footer>

</body>
</html>
```